"Cedar Hollow Realty" is the name of my real estate company

This is for a: "for sale" sign, looking for a minimalist design, wire frame outline of a midcentury modern homes roof line or elevation?

My name is: Dean Marlowe (needed)
My Cell # is: 415 208 3947 (needed)
My BRE license # is: 02468135 (needed)
BRE needs to be displayed in this format: BRE 02468135 (needed)
The white outline on the sign riders 'pictured" may work on large sign
Note font on pictured rider sign

This design is for a real estate "for sale" sign or sandwich board sign. Do Not include the words "For Sale" on the sign.

The measurements are 36" inches (91.44 cm) Length, or tall X 24" inches (60.90 cm) Wide.

|
3
---- 24 ----
6
|

Sorry I wasn't more specific earlier. I'd like the elements of the sign to be scaled in size according to their importance, from largest to smallest:

My name: Dean Marlowe
My phone number: 415-208-3947
My company name: Cedar Hollow Realty
My license number: BRE 02468135 (This can be much smaller than the smallest text)
Additionally, please incorporate contemporary to mid-century modern elements on the wire frame roofline or a simple roof-like design.

Thank you!

Best regards,
Dean

```html
<!DOCTYPE html>
<html lang="en">
<head>
<meta charset="utf-8">
<title>Dean Marlowe – Yard Sign</title>
<link rel="stylesheet" href="https://fonts.googleapis.com/css2?family=Jost:wght@400;500;600&display=swap">
<style>
  :root {
    --backdrop: #e6e6e3;
    --sign-black: #000000;
    --panel-black: #0c0c0c;
    --sign-white: #ffffff;
    --ink: #111111;
  }
  html, body {
    margin: 0;
    padding: 0;
    width: 1200px;
    height: 1123px;
    overflow: hidden;
    background: var(--backdrop);
  }
  .canvas {
    position: relative;
    width: 1200px;
    height: 1123px;
  }
  .sign {
    position: absolute;
    left: 56px;
    top: 220px;
    width: 1089px;
    height: 728px;
    background: var(--sign-black);
  }
  .sign-frame {
    position: absolute;
    left: 20px;
    top: 20px;
    right: 20px;
    bottom: 20px;
    border: 2px solid var(--sign-white);
  }
  .name-panel {
    position: absolute;
    left: 22px;
    top: 22px;
    width: 773px;
    height: 684px;
    background: var(--panel-black);
    font-family: "Jost", "Futura", sans-serif;
    color: var(--sign-white);
  }
  .agent-name {
    position: absolute;
    left: 52px;
    top: 60px;
    margin: 0;
    font-weight: 500;
    font-size: 134px;
    line-height: 190px;
    letter-spacing: 0;
    text-transform: uppercase;
    white-space: nowrap;
  }
  .agent-name span { display: block; }
  .agent-phone {
    position: absolute;
    left: 54px;
    top: 498px;
    margin: 0;
    font-weight: 600;
    font-size: 100px;
    line-height: 1;
    letter-spacing: -2px;
    word-spacing: -4px;
    white-space: nowrap;
  }
  .license-panel {
    position: absolute;
    left: 795px;
    top: 22px;
    width: 272px;
    height: 684px;
    background: var(--sign-white);
    font-family: "Jost", "Futura", sans-serif;
    color: var(--ink);
  }
  .roofline {
    position: absolute;
    left: 46px;
    top: 60px;
    width: 180px;
    height: 80px;
  }
  .company-name {
    position: absolute;
    left: 0;
    right: 0;
    top: 158px;
    margin: 0;
    text-align: center;
    font-weight: 500;
    font-size: 38px;
    line-height: 46px;
    letter-spacing: 1px;
    text-transform: uppercase;
  }
  .company-name span { display: block; }
  .license-rule {
    position: absolute;
    left: 135px;
    top: 325px;
    width: 2px;
    height: 120px;
    background: var(--ink);
  }
  .license-number {
    position: absolute;
    left: 0;
    right: 0;
    top: 472px;
    margin: 0;
    text-align: center;
    font-weight: 400;
    font-size: 28px;
    line-height: 38px;
    letter-spacing: 0.5px;
  }
  .license-number span { display: block; }
</style>
</head>
<body>
  <main class="canvas">
    <section class="sign" aria-label="Agent yard sign">
      <div class="sign-frame"></div>
      <div class="name-panel">
        <h1 class="agent-name"><span>Dean</span><span>Marlowe</span></h1>
        <p class="agent-phone">415 208 3947</p>
      </div>
      <div class="license-panel">
        <svg class="roofline" viewBox="0 0 180 80" aria-hidden="true">
          <g fill="none" stroke="#111111" stroke-width="3" stroke-linecap="square" stroke-linejoin="miter">
            <polyline points="4,14 90,38 176,4"/>
            <line x1="24" y1="20" x2="24" y2="76"/>
            <line x1="156" y1="12" x2="156" y2="76"/>
            <line x1="90" y1="38" x2="90" y2="76"/>
            <line x1="10" y1="76" x2="170" y2="76"/>
          </g>
        </svg>
        <p class="company-name"><span>Cedar</span><span>Hollow</span><span>Realty</span></p>
        <div class="license-rule"></div>
        <p class="license-number"><span>BRE</span><span>02468135</span></p>
      </div>
    </section>
  </main>
</body>
</html>
```